I need new business cards designed

I would like to get some new designs on business cards. I will upload my logo for reference. The business cards that were designed for me a few months ago were too difficult for the print companies to work with. My company is Quillbrook.net LLC. It is an art company that sells painting and expression cards online.

```html
<!DOCTYPE html>
<html lang="en">
<head>
<meta charset="utf-8">
<title>Quillbrook.net LLC — Business Cards</title>
<link href="https://fonts.googleapis.com/css2?family=Open+Sans:wght@400;600;700&display=swap" rel="stylesheet">
<style>
  :root {
    --backdrop: #1c1c1e;
    --card: #ffffff;
    --edge-blue: #1499d8;
    --navy: #2e3382;
    --sky: #0f9bd7;
    --ink: #2b2b2b;
  }
  * { box-sizing: border-box; margin: 0; padding: 0; }
  html, body {
    width: 1200px; height: 900px; overflow: hidden;
    background: var(--backdrop);
    font-family: "Open Sans", sans-serif;
  }
  .sheet {
    width: 1200px; height: 900px;
    display: flex; flex-direction: column;
    align-items: center; justify-content: center; gap: 70px;
  }
  .card {
    width: 560px; height: 320px;
    background: var(--card);
    border-radius: 22px;
    box-shadow: 0 4px 0 var(--edge-blue), 0 8px 0 #0d7fb6, 0 18px 30px rgba(0,0,0,.5);
    position: relative;
  }
  /* Front */
  .front { display: flex; align-items: center; justify-content: center; gap: 22px; }
  .brand-square { width: 92px; height: 92px; background: var(--navy); }
  .brand-name {
    font-weight: 600; font-size: 46px; color: var(--navy); letter-spacing: .5px;
  }
  .social-handle {
    position: absolute; right: 30px; top: 34px;
    font-size: 13px; font-weight: 600; color: var(--sky);
  }
  /* Back */
  .back { display: flex; align-items: center; padding: 0 36px; }
  .back-brand { display: flex; align-items: center; gap: 10px; width: 228px; }
  .back-brand .brand-square { width: 38px; height: 38px; }
  .back-brand .brand-name { font-size: 22px; }
  .divider { width: 2px; height: 150px; background: var(--sky); margin: 0 22px 0 12px; }
  .contact { color: var(--ink); font-size: 13.5px; line-height: 1.5; }
  .contact-name { color: var(--sky); font-weight: 700; font-size: 22px; letter-spacing: .5px; line-height: 1.2; }
  .contact-title { margin-bottom: 8px; }
  .contact-address { margin-bottom: 8px; }
  .contact-line { display: flex; align-items: center; gap: 8px; }
  .contact-line svg { width: 13px; height: 13px; fill: var(--sky); flex: none; }
</style>
</head>
<body>
<main class="sheet">
  <section class="card front">
    <div class="brand-square"></div>
    <div class="brand-name">Quillbrook.net</div>
    <div class="social-handle">@quillbrook</div>
  </section>

  <section class="card back">
    <div class="back-brand">
      <div class="brand-square"></div>
      <div class="brand-name">Quillbrook.net</div>
    </div>
    <div class="divider"></div>
    <div class="contact">
      <div class="contact-name">NORA WHITFIELD</div>
      <div class="contact-title">Managing Director</div>
      <div class="contact-address">Your address, City<br>State, Zip 1234</div>
      <div class="contact-line">
        <svg viewBox="0 0 24 24" aria-hidden="true"><path d="M6.6 10.8a15.5 15.5 0 0 0 6.6 6.6l2.2-2.2c.3-.3.7-.4 1-.2 1.1.4 2.3.6 3.6.6.6 0 1 .4 1 1V20c0 .6-.4 1-1 1A17 17 0 0 1 3 4c0-.6.4-1 1-1h3.5c.6 0 1 .4 1 1 0 1.3.2 2.5.6 3.6.1.3 0 .7-.2 1z"/></svg>
        555-214-7730
      </div>
      <div class="contact-line">
        <svg viewBox="0 0 24 24" aria-hidden="true"><path d="M2 5h20v14H2z M3 6l9 7 9-7" fill="none" stroke="#0f9bd7" stroke-width="2"/></svg>
        hello@quillbrook.net
      </div>
      <div class="contact-line">
        <svg viewBox="0 0 24 24" aria-hidden="true"><circle cx="12" cy="12" r="10" fill="none" stroke="#0f9bd7" stroke-width="2"/><path d="M2 12h20M12 2c3 3 3 17 0 20M12 2c-3 3-3 17 0 20" fill="none" stroke="#0f9bd7" stroke-width="1.6"/></svg>
        www.Quillbrook.net
      </div>
    </div>
  </section>
</main>
</body>
</html>
```